Venture 482 - Lumora Book Cover

I am looking for a Lumora book cover for my book about "Venture 482".
The Book is Titled:
Venture 482 Ascended
Shaping Outcomes: Paths To Unlocking Cosmic Truths
Author is Dorian Pell
Here is a book description that may help you understand more about it:
Inspired by the genius of Edwin Marlowe, this comprehensive guide delves into the ancient wisdom and cutting-edge science behind the 482 method, a powerful tool for manifesting your desires. Whether you're seeking personal growth, financial success, or spiritual enlightenment, this book provides advanced techniques and methods to transform your dreams into reality.
Any questions please ask.
Thanks
Owen

```html
<!DOCTYPE html>
<html lang="en">
<head>
<meta charset="utf-8">
<title>Venture 482 Ascended — Dorian Pell</title>
<link rel="stylesheet" href="https://fonts.googleapis.com/css2?family=Cinzel:wght@400;500&family=Tinos:wght@400;700&display=swap">
<style>
  :root {
    --sky-deep: #1b1438;
    --sky-mid: #2a2156;
    --sky-haze: #4a4478;
    --ring-teal: #5a97aa;
    --cream: #fbefe6;
    --band: #fbf6d8;
    --band-ink: #2c2552;
    --white: #ffffff;
    --author: #f2dcd3;
  }
  * { margin: 0; padding: 0; box-sizing: border-box; }
  html, body { width: 805px; height: 1200px; overflow: hidden; background: var(--sky-deep); }
  .cover { position: relative; width: 805px; height: 1200px; overflow: hidden; }
  .cover__art { position: absolute; inset: 0; width: 805px; height: 1200px; }
  .cover__title-top {
    position: absolute; left: 0; right: 0; top: 312px; text-align: center;
    font-family: "Cinzel", serif; font-weight: 400; font-size: 96px;
    letter-spacing: 2px; color: var(--cream); line-height: 1;
  }
  .cover__number {
    position: absolute; left: 0; right: 0; top: 418px; text-align: center;
    font-family: "Cinzel", serif; font-weight: 400; font-size: 214px;
    color: var(--cream); line-height: 1; letter-spacing: -4px;
  }
  .cover__band {
    position: absolute; left: 171px; top: 638px; width: 462px; height: 57px;
    background: var(--band); display: flex; align-items: center; justify-content: center;
    font-family: "Cinzel", serif; font-size: 38px; color: var(--band-ink);
    letter-spacing: 24px; padding-left: 24px;
  }
  .cover__subtitle {
    position: absolute; left: 0; right: 0; top: 946px; text-align: center;
    font-family: "Tinos", serif; color: var(--white); line-height: 40px;
  }
  .cover__subtitle-lead { display: block; font-weight: 700; font-size: 31px; }
  .cover__subtitle-rest { display: block; font-weight: 400; font-size: 29px; }
  .cover__author {
    position: absolute; left: 0; right: 0; top: 1112px; text-align: center;
    font-family: "Cinzel", serif; font-size: 44px; letter-spacing: 15px;
    padding-left: 15px; color: var(--author); line-height: 1;
  }
</style>
</head>
<body>
<main class="cover">
  <svg class="cover__art" viewBox="0 0 805 1200" role="img" aria-label="Starry night sky with a swirling ring of scattered numerals and faint constellation lines">
    <defs>
      <linearGradient id="sky" x1="0" y1="0" x2="1" y2="1">
        <stop offset="0" stop-color="#3a3468"/>
        <stop offset="0.35" stop-color="var(--sky-mid)"/>
        <stop offset="1" stop-color="var(--sky-deep)"/>
      </linearGradient>
      <radialGradient id="haze" cx="0.2" cy="0.05" r="0.6">
        <stop offset="0" stop-color="var(--sky-haze)" stop-opacity="0.7"/>
        <stop offset="1" stop-color="var(--sky-haze)" stop-opacity="0"/>
      </radialGradient>
      <radialGradient id="ring" cx="0.5" cy="0.5" r="0.5">
        <stop offset="0.68" stop-color="var(--ring-teal)" stop-opacity="0"/>
        <stop offset="0.84" stop-color="var(--ring-teal)" stop-opacity="0.35"/>
        <stop offset="1" stop-color="var(--ring-teal)" stop-opacity="0"/>
      </radialGradient>
    </defs>
    <rect width="805" height="1200" fill="url(#sky)"/>
    <rect width="805" height="1200" fill="url(#haze)"/>
    <circle cx="403" cy="548" r="375" fill="url(#ring)"/>
  </svg>

  <h1 class="cover__title">
    <span class="cover__title-top">VENTURE</span>
    <span class="cover__number">482</span>
    <span class="cover__band">ASCENDED</span>
  </h1>

  <p class="cover__subtitle">
    <span class="cover__subtitle-lead">SHAPING OUTCOMES:</span>
    <span class="cover__subtitle-rest">Paths to unlocking</span>
    <span class="cover__subtitle-rest">cosmic truths</span>
  </p>

  <p class="cover__author">DORIAN PELL</p>
</main>
</body>
</html>
```